4th Generation Family Business Needs a New Card Design!

We are a family owned 4th Generation company. We are based in the Sydney, Australia area and we are desperately in need of a more modern and classy card. We are monumental masons who design, supply & erect lasting memorials throughout cemeteries in Sydney. Our customers are normally in a period of grieving. I have attached logo files that will need to be implemented on the card. Company was established 1935. Australian Owned and Operated. Card needs to be designed to PIXO.com specification.

Target Market(s)

Our target market is based upon people that a grieving for family members that have passed away. We also deal with alot of companies that own and operate cemeteries.

Industry/Entity Type

Business

Contact Information for Business Card

Simon Harcourt, Operations Manager, 0417293086, simon@harcourtmemorials.com.au
Lewis Harcourt, Director, 0491630572, lewis@harcourtmemorials.com.au
Phone # 02 9561 3048
Website: www.harcourtmemorials.com.au
Address: Suite 17, 8 Palfrey Lane, West Carlow, Sydney NSW 2156

Font styles to use
Serif
Decorative
Script

Requirements
Must have
• Would like to see the logo nicely implemented with a modern design. Embossed lettering would be a nice additive.

```html
<!DOCTYPE html>
<html lang="en">
<head>
<meta charset="utf-8">
<title>Harcourt Memorials – Business Card</title>
<link href="https://fonts.googleapis.com/css2?family=Cinzel:wght@400;700&family=Open+Sans:wght@400&display=swap" rel="stylesheet">
<style>
  :root {
    --backdrop: #c9c9c9;
    --card: #222222;
    --card-edge: #161616;
    --gold: #f2b51c;
    --ink: #f1f1f1;
    --emboss: #2e2e2e;
    --emboss-light: #3a3a3a;
  }
  * { margin: 0; padding: 0; box-sizing: border-box; }
  html, body {
    width: 1200px; height: 844px; overflow: hidden;
    background: var(--backdrop);
  }
  .stage {
    position: relative; width: 1200px; height: 844px;
    display: flex; align-items: center; justify-content: center; gap: 56px;
  }
  .card {
    position: relative; width: 520px; height: 297px;
    background: var(--card);
    box-shadow: 0 10px 24px rgba(0,0,0,.28);
    font-family: "Open Sans", Arial, sans-serif; color: var(--ink);
  }

  /* Contact side */
  .mark-decoration {
    position: absolute; right: 70px; top: 30px; width: 150px; height: 120px;
    background: linear-gradient(135deg, var(--emboss-light), var(--emboss));
    box-shadow: inset 1px 1px 0 rgba(255,255,255,.08), inset -1px -1px 0 rgba(0,0,0,.4);
  }
  .person { position: absolute; left: 30px; }
  .person--first { top: 28px; }
  .person--second { top: 198px; }
  .person__name {
    font-family: "Cinzel", Georgia, serif; font-weight: 700;
    color: var(--gold); font-size: 17px; line-height: 1.2; font-variant: small-caps;
  }
  .person__role, .person__line { font-size: 13px; line-height: 1.45; }
  .person__line { display: flex; align-items: center; gap: 6px; }
  .icon { width: 10px; height: 10px; flex: none; fill: var(--gold); }
  .address {
    position: absolute; left: 30px; top: 136px; font-size: 13px; line-height: 1.45;
  }
  .company-lines {
    position: absolute; right: 26px; top: 170px; text-align: right;
    font-size: 13px; line-height: 1.6;
  }
  .company-lines .person__line { justify-content: flex-end; }

  /* Brand side */
  .brand {
    position: absolute; inset: 0;
    display: flex; align-items: center; justify-content: center;
  }
  .brand__name {
    font-family: "Cinzel", Georgia, serif; font-weight: 400;
    color: var(--ink); font-size: 30px; letter-spacing: 2px; text-align: center; line-height: 1.15;
  }
</style>
</head>
<body>
<main class="stage">
  <section class="card card--contacts" aria-label="Contact side">
    <div class="mark-decoration" role="img" aria-label="Embossed brand monogram area"></div>

    <div class="person person--first">
      <p class="person__name">Simon Harcourt</p>
      <p class="person__role">Operations Manager</p>
      <p class="person__line"><svg class="icon" viewBox="0 0 10 10"><rect x="2" y="0" width="6" height="10" rx="1"/></svg>0417293086</p>
      <p class="person__line"><svg class="icon" viewBox="0 0 10 10"><path d="M0 2h10v6H0z M0 2l5 3 5-3" /></svg>simon@harcourtmemorials.com.au</p>
    </div>

    <p class="address">Suite 17, 8 Palfrey Lane, West Carlow,<br>Sydney NSW 2156</p>

    <div class="person person--second">
      <p class="person__name">Lewis Harcourt</p>
      <p class="person__role">Director</p>
      <p class="person__line"><svg class="icon" viewBox="0 0 10 10"><rect x="2" y="0" width="6" height="10" rx="1"/></svg>0491630572</p>
      <p class="person__line"><svg class="icon" viewBox="0 0 10 10"><path d="M0 2h10v6H0z M0 2l5 3 5-3" /></svg>lewis@harcourtmemorials.com.au</p>
    </div>

    <div class="company-lines">
      <p class="person__line">02 9561 3048<svg class="icon" viewBox="0 0 10 10"><path d="M1 3h8v6H1z M0 1h10v2H0z"/></svg></p>
      <p class="person__line">www.harcourtmemorials.com.au<svg class="icon" viewBox="0 0 10 10"><circle cx="5" cy="5" r="5"/></svg></p>
    </div>
  </section>

  <section class="card card--brand" aria-label="Brand side">
    <div class="brand">
      <p class="brand__name">HARCOURT<br>MEMORIALS</p>
    </div>
  </section>
</main>
</body>
</html>
```